Bright Path Academy - Personal Development business 2.0 needs a social post format design.

https://www.brightpathacademy.example

Our focus with Bright Path Academy is on developing people through knowledge and skills to improve their everyday lives.
We love simplicity, Quince design and less is more.

We are crazy about personal growth, science, design, the latest gadgets and people.

We need 4 formats for our social media posts.
1. Blogs -to pronounce a blog post
2. Workshop /training - to pronounce our workshops/trainings (both online and offline)
3. Podcast - called "Kijk eens verder". To pronounce a guest we've spoken. The host is called Berend.
4. Facts - to pronounce short facts about personal development. Invites people to read more.
The formats should include: high quality pictogram (better than the uploaded picto's), 1 of the 3 logo's in the design.
It's important that we can edit the design in Affinity Design / Affinity Photo to adjust the text in the format.

Attached you find four of our current designs, which are a poor example of how the designs should look like. These are just to show you how much lines of text (more or less) will be in the designs. So please do not make a design that looks like these ;) You have carte blanche.

Our customers are mostly women (80%). We focus on both business and casual customers.

Target Market(s)

80% woman, 20% men. We focus on both business and casual customers.

Requirements
Must have
• Less is more. Quince Design alike. Simplicity.
Aimed at the women target audience.
Designs must be edible for adjusting the text in the format.
Nice to have
• Unique concept.
The design should "breathe".
Each design can have a different color, so customers identify the specific post with specific information. For example, blog is red, workshop post black, etc.

```html
<!DOCTYPE html>
<html lang="en">
<head>
<meta charset="utf-8">
<title>Sayings Post Template – Bright Path Academy</title>
<link href="https://fonts.googleapis.com/css2?family=Roboto+Condensed:wght@300;400;700&display=swap" rel="stylesheet">
<style>
  :root {
    --page-bg: #ffffff;
    --title-grey: #a9a9a9;
    --ink: #111111;
    --white: #ffffff;
    --spirit-blue: #0a84f0;
    --mind-orange: #ffa800;
    --icon-grey: #7a7a7a;
    --panel-dark: rgba(20, 20, 20, 0.72);
    --panel-light: rgba(120, 120, 120, 0.5);
  }
  * { box-sizing: border-box; margin: 0; padding: 0; }
  html, body { width: 1200px; height: 753px; overflow: hidden; background: var(--page-bg); }
  body { position: relative; font-family: "Roboto Condensed", sans-serif; }

  .sheet-title {
    position: absolute; top: 56px; left: 0; width: 1200px;
    text-align: center; font-weight: 300; font-size: 48px;
    letter-spacing: 1.5px; color: var(--title-grey);
  }

  .post { position: absolute; top: 159px; width: 524px; height: 524px; overflow: hidden; }
  .post--spirit { left: 47px; }
  .post--mind { left: 629px; }

  .post__photo { position: absolute; inset: 0; }
  .post--spirit .post__photo {
    background:
      radial-gradient(ellipse 40% 55% at 20% 45%, rgba(30,30,30,0.75), transparent 70%),
      linear-gradient(180deg, #5a5a5a 0%, #cfcfcf 12%, #8d8d8d 28%, #6b6b6b 45%, #9a9a9a 60%, #3f3f3f 80%, #2a2a2a 100%);
  }
  .post--mind .post__photo {
    background:
      linear-gradient(180deg, #dfe6ea 0%, #eef0ec 22%, #e9dcc4 40%, #a88a62 52%, #5e4a36 64%, #3f342c 78%, #5b5a63 90%, #3a3740 100%);
  }

  .post__brand {
    position: absolute; top: 56px; left: 0; width: 100%;
    text-align: center; font-weight: 700; font-size: 30px; color: var(--ink);
    letter-spacing: 0.5px;
  }

  .post__panel {
    position: absolute; left: 32px; top: 155px; width: 461px; height: 282px;
    border-radius: 30px;
  }
  .post--spirit .post__panel { background: var(--panel-dark); }
  .post--mind .post__panel { background: var(--panel-light); }

  .quote-mark { position: absolute; width: 66px; height: 64px; }
  .post--spirit .quote-mark { fill: var(--spirit-blue); }
  .post--mind .quote-mark { fill: var(--mind-orange); }
  .post--spirit .quote-mark--open { left: 19px; top: 145px; }
  .post--spirit .quote-mark--close { left: 440px; top: 376px; }
  .post--mind .quote-mark--open { left: 30px; top: 189px; }
  .post--mind .quote-mark--close { left: 409px; top: 315px; }

  .post__quote {
    position: absolute; left: 0; width: 524px; text-align: center;
    color: var(--white); font-weight: 700; letter-spacing: -0.6px;
    text-shadow: 0 2px 4px rgba(0,0,0,0.45);
  }
  .post--spirit .post__quote { top: 208px; font-size: 35px; line-height: 42px; }
  .post--mind .post__quote { top: 217px; font-size: 36px; line-height: 44px; padding-left: 8px; }

  .topics {
    position: absolute; top: 400px; left: 0; width: 524px;
    display: flex; justify-content: center; gap: 6px; list-style: none;
  }
  .topic { width: 48px; display: flex; flex-direction: column; align-items: center; }
  .topic__badge {
    width: 46px; height: 46px; border-radius: 50%;
    background: var(--icon-grey); border: 2px solid rgba(255,255,255,0.35);
    display: flex; align-items: center; justify-content: center;
  }
  .topic__badge svg { width: 30px; height: 30px; fill: none; stroke: var(--white); stroke-width: 1.4; stroke-linecap: round; stroke-linejoin: round; }
  .post--spirit .topic--active .topic__badge { background: var(--spirit-blue); }
  .post--mind .topic--active .topic__badge { background: var(--mind-orange); }
  .topic__label {
    margin-top: 6px; font-size: 13px; font-weight: 700; color: var(--white);
    white-space: nowrap; text-shadow: 0 1px 2px rgba(0,0,0,0.5);
  }

  .post__url {
    position: absolute; top: 490px; left: 0; width: 100%; text-align: center;
    font-size: 13px; letter-spacing: 1.2px; color: var(--white);
  }
</style>
</head>
<body>
  <h1 class="sheet-title">SAYINGS POST TEMPLATE</h1>

  <svg width="0" height="0" style="position:absolute" aria-hidden="true">
    <defs>
      <path id="mark-half" d="M0,64 V30 C0,12 9,2 27,0 V13 C19,16 15,22 15,31 H30 V64 Z"/>
      <g id="icon-body"><path d="M15 25 C6 18 3 14 3 10 A5.5 5.5 0 0 1 15 7 A5.5 5.5 0 0 1 27 10 C27 14 24 18 15 25 Z"/><path d="M4 15 H10 L12 11 L15 19 L18 13 H26"/></g>
      <g id="icon-mind"><path d="M15 5 C11 3 7 5 7 9 C4 10 3 14 5 16 C3 19 5 23 9 23 C10 26 14 26 15 24 C16 26 20 26 21 23 C25 23 27 19 25 16 C27 14 26 10 23 9 C23 5 19 3 15 5 Z"/><path d="M15 5 V24 M10 12 C12 12 13 14 13 16 M20 12 C18 12 17 14 17 16 M9 19 H12 M18 19 H21"/></g>
      <g id="icon-spirit"><circle cx="15" cy="15" r="11"/><circle cx="15" cy="15" r="7"/><path d="M15 11 A4 4 0 1 1 11 15"/></g>
      <g id="icon-skills"><circle cx="15" cy="15" r="4"/><path d="M13 3 H17 L18 7 L21 8.5 L24.5 6.5 L27 9.5 L25 13 L26 16 L28 17 V13 M28 13 V17 L26 18 L25 21 L27 24 L24.5 27 L21 25 L18 26.5 L17 30 H13 L12 26.5 L9 25 L5.5 27 L3 24 L5 21 L4 18 L2 17 V13 L4 12 L5 9 L3 6 L5.5 3.5 L9 5.5 L12 4 Z"/></g>
      <g id="icon-business"><rect x="3" y="9" width="24" height="17" rx="2"/><path d="M11 9 V6 H19 V9 M3 16 H27 M13 16 V18 H17 V16"/></g>
    </defs>
  </svg>

  <article class="post post--spirit">
    <div class="post__photo" role="img" aria-label="Black and white photo of a man in profile looking out over a lake"></div>
    <p class="post__brand">Bright Path Academy</p>
    <div class="post__panel"></div>
    <svg class="quote-mark quote-mark--open" viewBox="0 0 66 64"><use href="#mark-half"/><use href="#mark-half" x="36"/></svg>
    <svg class="quote-mark quote-mark--close" viewBox="0 0 66 64"><g transform="rotate(180 33 32)"><use href="#mark-half"/><use href="#mark-half" x="36"/></g></svg>
    <p class="post__quote">I am never in control of<br>what happens around me,<br>but i am always in control of<br>what happens within me.</p>
    <ul class="topics">
      <li class="topic"><span class="topic__badge"><svg viewBox="0 0 30 30"><use href="#icon-body"/></svg></span><span class="topic__label">BODY</span></li>
      <li class="topic"><span class="topic__badge"><svg viewBox="0 0 30 30"><use href="#icon-mind"/></svg></span><span class="topic__label">MIND</span></li>
      <li class="topic topic--active"><span class="topic__badge"><svg viewBox="0 0 30 30"><use href="#icon-spirit"/></svg></span><span class="topic__label">SPIRIT</span></li>
      <li class="topic"><span class="topic__badge"><svg viewBox="0 0 30 30"><use href="#icon-skills"/></svg></span><span class="topic__label">SKILLS</span></li>
      <li class="topic"><span class="topic__badge"><svg viewBox="0 0 30 30"><use href="#icon-business"/></svg></span><span class="topic__label">BUSINESS</span></li>
    </ul>
    <p class="post__url">www.brightpathacademy.example</p>
  </article>

  <article class="post post--mind">
    <div class="post__photo" role="img" aria-label="Photo of friends walking on a rocky hilltop at sunset"></div>
    <p class="post__brand">Bright Path Academy</p>
    <div class="post__panel"></div>
    <svg class="quote-mark quote-mark--open" viewBox="0 0 66 64"><use href="#mark-half"/><use href="#mark-half" x="36"/></svg>
    <svg class="quote-mark quote-mark--close" viewBox="0 0 66 64"><g transform="rotate(180 33 32)"><use href="#mark-half"/><use href="#mark-half" x="36"/></g></svg>
    <p class="post__quote">Sometimes the secret<br>to getting more done<br>is to take time off.</p>
    <ul class="topics">
      <li class="topic"><span class="topic__badge"><svg viewBox="0 0 30 30"><use href="#icon-body"/></svg></span><span class="topic__label">BODY</span></li>
      <li class="topic topic--active"><span class="topic__badge"><svg viewBox="0 0 30 30"><use href="#icon-mind"/></svg></span><span class="topic__label">MIND</span></li>
      <li class="topic"><span class="topic__badge"><svg viewBox="0 0 30 30"><use href="#icon-spirit"/></svg></span><span class="topic__label">SPIRIT</span></li>
      <li class="topic"><span class="topic__badge"><svg viewBox="0 0 30 30"><use href="#icon-skills"/></svg></span><span class="topic__label">SKILLS</span></li>
      <li class="topic"><span class="topic__badge"><svg viewBox="0 0 30 30"><use href="#icon-business"/></svg></span><span class="topic__label">BUSINESS</span></li>
    </ul>
    <p class="post__url">www.brightpathacademy.example</p>
  </article>
</body>
</html>
```